Company Website Re-design for Software development consultancy

We would like our company website to be redesigned using our existing marketing collateral and website content as a guide

current site : www.brightkestrel.com.au

For the different pages types and content please base on the following site : https://www.quorvalabs.net/

We want a coded site - but will replace the content ourselves within the sections you provide to customise to our needs.

Target Market(s)

Medium to Large corporates needing software design and development services

Industry/Entity Type

Information Technology

Coding

Coded - Design and coding required

Number of Pages Required

5+ page

Font styles to use
Sans Serif

Colors
ec1f27
ffffff
000000

Requirements
Must have
• Align to colour scheme of existing collateral
• Include pages for the key areas of our busines - see : https://www.quorvalabs.net/
Nice to have
• image rotators - make the site interesting to the business visitor

```html
<!DOCTYPE html>
<html lang="en">
<head>
<meta charset="utf-8">
<title>Bright Kestrel – Building Software Better</title>
<link href="https://fonts.googleapis.com/css2?family=Open+Sans:ital,wght@0,400;0,600;0,700;0,800;1,400&display=swap" rel="stylesheet">
<style>
:root{
  --red:#ec1f27;
  --black:#000;
  --white:#fff;
  --ink:#222;
  --text:#333;
  --muted:#555;
  --panel:#f2f2f2;
  --ghost:#e2e2e2;
  --ghost-light:#ececec;
  --grey-dot:#c8c8c8;
}
*{box-sizing:border-box;margin:0;padding:0}
html,body{width:1200px;height:2612px;overflow:hidden;background:var(--white)}
body{position:relative;font-family:"Open Sans",Arial,sans-serif;color:var(--text)}
.abs{position:absolute}
.center{left:0;width:1200px;text-align:center}

/* header */
.site-header{position:absolute;top:0;left:0;width:1200px;height:72px;background:var(--white)}
.brand{position:absolute;display:flex;align-items:center;gap:10px}
.brand-dot{width:52px;height:52px;border-radius:50%;background:var(--red)}
.brand-name{font-weight:800;color:var(--red);font-size:30px;letter-spacing:.5px;text-transform:uppercase}
.menu-toggle{position:absolute;left:1070px;top:27px;width:30px}
.menu-toggle span{display:block;height:3px;background:#888;margin-bottom:5px;border-radius:2px}

/* hero */
.hero{position:absolute;top:72px;left:0;width:1200px;height:588px;
  background:radial-gradient(ellipse at 45% 60%,#6a6a5e 0%,#3e3c38 45%,#1e1d1c 100%)}
.hero-title{top:270px;font-size:52px;font-weight:700;color:var(--white);letter-spacing:1px}
.hero-sub{top:340px;font-size:15px;color:var(--white)}
.hero-dots{position:absolute;left:549px;top:517px;width:102px;height:28px;border-radius:6px;background:rgba(200,200,200,.75);
  display:flex;justify-content:center;align-items:center;gap:6px}
.hero-dots i{width:11px;height:11px;border-radius:50%;background:#111}
.hero-dots i.on{background:var(--white)}
.social-rail{position:absolute;left:1158px;top:154px;display:flex;flex-direction:column;gap:16px}
.social-rail i{width:24px;height:24px;border-radius:50%;display:block}

/* sections */
.section-title{font-size:31px;color:var(--ink);font-weight:400;letter-spacing:.3px}
.ghost{font-weight:800;color:var(--ghost);white-space:nowrap;text-transform:uppercase}
.rule{position:absolute;left:568px;width:64px;height:3px;background:var(--black)}
.btn{position:absolute;background:var(--red);color:var(--white);font-weight:700;font-size:17px;
  height:45px;width:129px;display:flex;align-items:center;justify-content:center}

.about{position:absolute;top:660px;left:0;width:1200px;height:277px;background:var(--panel)}
.about p{position:absolute;left:78px;width:1044px;top:110px;font-size:13.6px;line-height:25px;text-align:center}

.card{position:absolute;width:284px;background:var(--panel);text-align:center}
.card h3{font-size:21px;font-weight:600;color:var(--ink)}
.card p{font-size:13.6px;line-height:25px;color:var(--muted)}
.card svg{display:block;margin:0 auto}

.team-card{position:absolute;top:1688px;width:284px;height:359px;background:var(--panel);text-align:center}
.team-card.featured{box-shadow:0 6px 10px rgba(0,0,0,.18)}
.portrait{width:131px;height:131px;border-radius:50%;margin:30px auto 0;background:radial-gradient(circle at 50% 40%,#b89a86 0%,#6d6560 55%,#2c2f36 100%)}
.team-card h4{margin-top:22px;font-size:18px;font-weight:600;color:var(--ink)}
.team-card .role{margin-top:4px;font-size:12px;font-style:italic;color:var(--muted)}
.team-card .quote{margin:8px auto 0;width:220px;font-size:15px;font-style:italic;line-height:26px;color:var(--ink)}
.team-card .profile{width:22px;height:22px;border-radius:50%;background:#1c6fb7;margin:12px auto 0}
.pager{position:absolute;top:2098px;left:565px;display:flex;gap:13px}
.pager i{width:14px;height:14px;background:var(--grey-dot);display:block}

.contact{position:absolute;top:2150px;left:0;width:1200px;height:270px;background:var(--panel)}
.contact-item{position:absolute;top:146px;display:flex;gap:14px}
.contact-icon{width:52px;height:52px;background:var(--red);display:flex;align-items:center;justify-content:center}
.contact-item h5{font-size:22px;font-weight:600;color:var(--ink);line-height:26px}
.contact-item span{font-size:13px;color:var(--muted);text-transform:uppercase}

.site-footer{position:absolute;top:2420px;left:0;width:1200px;height:192px}
.footer-nav{position:absolute;top:112px;left:88px;display:flex;gap:36px;font-size:14px;color:var(--ink)}
.copyright{position:absolute;top:146px;left:88px;font-size:11px;color:var(--muted)}
.follow{position:absolute;left:955px;top:74px;font-size:14px;font-weight:700;color:var(--ink)}
.follow-icons{position:absolute;left:953px;top:108px;display:flex;gap:8px}
.follow-icons i{width:24px;height:24px;border-radius:50%;display:block}
.c1{background:#5bb5e8}.c2{background:#f0892b}.c3{background:#1c6fb7}.c4{background:#555}.c5{background:#3b5ca8}
</style>
</head>
<body>

<header class="site-header">
  <div class="brand" style="left:97px;top:10px">
    <span class="brand-dot"></span><span class="brand-name">Bright Kestrel</span>
  </div>
  <div class="menu-toggle"><span></span><span></span><span></span></div>
</header>

<section class="hero" role="img" aria-label="Team working over a table covered in sticky notes and printed plans">
  <h1 class="abs center hero-title">BRIGHT KESTREL</h1>
  <p class="abs center hero-sub">Building Software Better</p>
  <div class="hero-dots"><i></i><i class="on"></i><i></i><i></i></div>
  <div class="social-rail"><i class="c1"></i><i class="c2"></i><i class="c3"></i><i class="c4"></i><i class="c5"></i></div>
</section>

<section class="about">
  <div class="abs center ghost" style="top:22px;font-size:50px">Welcome</div>
  <h2 class="abs center section-title" style="top:38px">ABOUT US</h2>
  <div class="rule" style="top:92px"></div>
  <p>After spending more than twenty years each in the industry, including seven years in New York building electronic trading systems for Harlow Beckett – the founders realised that there was a distinct lack in the market of people focusing on how software is developed – not just solving the business problem, but automating the development itself to increase both productivity and quality.</p>
  <a class="btn" style="left:535px;top:205px">Read more</a>
</section>

<section class="services">
  <div class="abs center ghost" style="top:958px;font-size:54px;color:var(--ghost-light)">The Three Faces of Bright Kestrel</div>
  <h2 class="abs center section-title" style="top:978px">WE ARE ALL ABOUT BUILDING SOFTWARE BETTER.</h2>
  <div class="rule" style="top:1032px"></div>

  <article class="card" style="left:144px;top:1066px;height:320px">
    <svg style="margin-top:50px" width="100" height="72" viewBox="0 0 100 72" aria-hidden="true">
      <circle cx="50" cy="16" r="14" fill="#111"/><circle cx="20" cy="26" r="10" fill="#111"/><circle cx="80" cy="26" r="10" fill="#111"/>
      <path d="M28 70 Q28 36 50 36 Q72 36 72 70 Z" fill="#111"/>
      <path d="M2 62 Q2 40 20 40 Q30 40 34 46 Q26 54 26 62 Z" fill="#111"/>
      <path d="M98 62 Q98 40 80 40 Q70 40 66 46 Q74 54 74 62 Z" fill="#111"/>
    </svg>
    <h3 style="margin-top:18px">Consulting</h3>
    <p style="margin:6px auto 0;width:240px">Up-skill your team by using our consultants - for either short or long term engagements.</p>
  </article>
  <a class="btn" style="left:222px;top:1388px">Read more</a>

  <article class="card" style="left:457px;top:1066px;height:320px">
    <svg style="margin-top:50px" width="80" height="64" viewBox="0 0 80 64" aria-hidden="true">
      <path d="M2 2 V62 H78" stroke="#111" stroke-width="5" fill="none"/>
      <rect x="16" y="34" width="8" height="20" fill="#111"/><rect x="30" y="24" width="8" height="30" fill="#111"/>
      <rect x="44" y="30" width="8" height="24" fill="#111"/><rect x="58" y="12" width="8" height="42" fill="#111"/>
    </svg>
    <h3 style="margin-top:18px">Projects</h3>
    <p style="margin:6px auto 0;width:240px">We can deliver a large project on a fixed price basis at a quality standard you won't believe</p>
  </article>
  <a class="btn" style="left:535px;top:1388px">Read more</a>

  <article class="card" style="left:771px;top:1066px;height:320px">
    <svg style="margin-top:54px" width="80" height="60" viewBox="0 0 80 60" aria-hidden="true">
      <path d="M2 6 Q2 2 6 2 H28 L36 10 H74 Q78 10 78 14 V56 Q78 58 74 58 H6 Q2 58 2 54 Z" fill="#111"/>
    </svg>
    <h3 style="margin-top:14px">Tabulo</h3>
    <p style="margin:6px auto 0;width:240px">Our product, Tabulo, allows you to skip the development cycle and turn a plain spreadsheet directly into either a web service or a web site</p>
  </article>
  <a class="btn" style="left:848px;top:1388px">Read more</a>
</section>

<section class="team">
  <div class="abs center ghost" style="top:1490px;font-size:54px;color:var(--ghost-light)">Meet Our Leadership Team</div>
  <h2 class="abs center section-title" style="top:1512px">MEET OUR LEADERSHIP TEAM</h2>
  <div class="rule" style="top:1567px"></div>
  <p class="abs" style="left:130px;width:940px;top:1598px;font-size:13.6px;line-height:26px;text-align:center">Between just the partners, we have more than 60 years of software development experience. We combine a solid knowledge of computer science with a practical, pragmatic approach to delivering software.</p>

  <article class="team-card" style="left:144px">
    <div class="portrait" role="img" aria-label="Portrait of Owen Marsh"></div>
    <h4>Owen Marsh</h4><p class="role">Partner</p>
    <p class="quote">Owen's one of the best developers on the planet</p>
    <div class="profile"></div>
  </article>
  <article class="team-card featured" style="left:457px">
    <div class="portrait" role="img" aria-label="Portrait of Liam Corder"></div>
    <h4>Liam Corder</h4><p class="role">Partner</p>
    <p class="quote">Liam's been running software projects for 20 years</p>
    <div class="profile"></div>
  </article>
  <article class="team-card" style="left:771px">
    <div class="portrait" role="img" aria-label="Portrait of Neil Pryce"></div>
    <h4>Neil Pryce</h4><p class="role">Partner</p>
    <p class="quote">Neil codes for fun as much as he does for work</p>
    <div class="profile"></div>
  </article>
  <div class="pager"><i></i><i></i><i></i></div>
</section>

<section class="contact">
  <h2 class="abs center" style="top:42px;font-size:36px;font-weight:400;color:var(--ink)">GET IN TOUCH</h2>
  <p class="abs center" style="top:103px;font-size:15px;color:var(--muted)">Bright Kestrel is based in Sydney Australia</p>
  <div class="contact-item" style="left:239px">
    <div class="contact-icon"><svg width="18" height="24" viewBox="0 0 18 24" aria-hidden="true"><path d="M9 0 A9 9 0 0 1 18 9 C18 15 9 24 9 24 C9 24 0 15 0 9 A9 9 0 0 1 9 0Z" fill="#fff"/><circle cx="9" cy="9" r="3.5" fill="#ec1f27"/></svg></div>
    <div><h5>FIND US AT THE OFFICE</h5><span>42 Harbour Lane, Sydney 2000</span></div>
  </div>
  <div class="contact-item" style="left:643px">
    <div class="contact-icon"><svg width="24" height="18" viewBox="0 0 24 18" aria-hidden="true"><rect x="1.5" y="1.5" width="21" height="15" fill="none" stroke="#fff" stroke-width="2.5"/><path d="M2 2 L12 10 L22 2" fill="none" stroke="#fff" stroke-width="2.5"/></svg></div>
    <div><h5>GIVE US AN EMAIL</h5><span>info@brightkestrel.com.au</span></div>
  </div>
</section>

<footer class="site-footer">
  <div class="brand" style="left:86px;top:42px">
    <span class="brand-dot" style="width:54px;height:54px"></span><span class="brand-name" style="font-size:31px">Bright Kestrel</span>
  </div>
  <nav class="footer-nav"><span>HOME</span><span>TABULO HELP</span><span>TABULO MICRO-SERVICES PLATFORM</span></nav>
  <p class="copyright">© 2018 &nbsp;|&nbsp; www.brightkestrel.com.au</p>
  <p class="follow">Follow Us</p>
  <div class="follow-icons"><i class="c1"></i><i class="c2"></i><i class="c3"></i><i class="c4"></i><i class="c5"></i></div>
</footer>

</body>
</html>
```